Window Cleaning Leaflet

Hi everyone,

I need a leaflet (couldn't find 'leaflet' as an option when begining this project - so one sided only) to send out to coastal properties in South side Melbourne. The Flyer is aimed at high net individuals, mummies, business people etc who own these properties who don't have time to clean the windows themselves (often multiple levels) and want their home looking fabulous in time for Christmas and NY's celebrations.

I would really love a new and original design for a window washing leaflet. something outside of the norm that 'pops' and makes people feel happy when they look at it.

I guess a point of differentiation is that I'm a female working in a mans industry so appeal to mothers looking for someone who is 'reliable, trustworthy and understanding of peoples needs'.

I have made an outline of what I would like included in the leaflet, so if you could please take a look, feel free to change things around, wording and layout etc. If you can make it sound more professional please do so.

I would like the colours to be 'happy' colours, maybe with a silly season theme?

Overall aesthetically pleasing is a must, I find most window cleaning leaflets fairly mundane and boring, please feel free to think outside the box. The more original the better.

Target Market(s)

People who own large Melbourne homes in affluent suburbs, mainly suburbs with a lot of large coastal properties. Generally owned by high net worth individuals who just don't have tme to clean the windows themselves due to their profession or hectic lifestyles but can afford to pay someone else to do it.

Industry/Entity Type

Window Cleaning

Requirements
Must have
• 1) The name of the business - Kelda’s Window Washing Services
• 2) The coupon special and all details attached:
• Small Homes (up to 12 windows) $120
• Medium Homes (up to 16 windows) $180
• Large Homes (up to 20 windows, 2 storeys) $240
• 20% discount
• *Discount applicable to first time customers only.
• *All services include fly screen, sill and tracks cleaned as well as cobweb removal.
• *Houses with more than 20 windows (or two levels) will have an immediate quote provided upon inspection of the property with 20% discount applied.
• *Kelda’s Window Washing Services are fully insured.
• 3) My contact number - 0418 265 903

```html
<!DOCTYPE html>
<html lang="en">
<head>
<meta charset="utf-8">
<title>Kelda’s Window Washing Services – Leaflet</title>
<link href="https://fonts.googleapis.com/css2?family=Exo+2:wght@500&family=Roboto+Condensed:wght@700&family=Arimo:ital,wght@0,400;1,700&display=swap" rel="stylesheet">
<style>
  :root{
    --backdrop:#6f6f71;
    --paper:#ffffff;
    --cyan:#14b1d3;
    --blue:#0a78c0;
    --title-blue:#0d80c4;
    --pink:#e8509a;
    --ink:#222222;
    --rule:#c9c9c9;
  }
  *{margin:0;padding:0;box-sizing:border-box}
  html,body{width:864px;height:1200px;overflow:hidden;background:var(--backdrop)}
  .leaflet{
    position:absolute;left:77px;top:96px;width:710px;height:1007px;
    background:var(--paper);overflow:hidden;
    box-shadow:0 14px 30px rgba(0,0,0,.35);
    font-family:"Arimo",Arial,sans-serif;color:var(--ink);
  }
  .hero-photo{
    position:absolute;left:0;top:0;width:710px;height:470px;
    background:
      linear-gradient(180deg,rgba(255,255,255,0) 55%,#ffffff 100%),
      linear-gradient(100deg,#e8e2dc 0%,#c8a15a 14%,#ecebea 24%,#b02a2a 32%,#ece8e6 48%,#9aa59c 58%,#f2f0ee 68%,#b9413f 80%,#f1ecea 100%);
  }
  .discount-badge{
    position:absolute;left:41px;top:280px;width:176px;height:176px;border-radius:50%;
    background:var(--cyan);border:7px solid #fff;
    box-shadow:0 4px 10px rgba(0,0,0,.3);
    display:flex;flex-direction:column;align-items:center;justify-content:center;
    color:#fff;font-family:"Roboto Condensed",Arial Narrow,sans-serif;font-weight:700;
    transform:rotate(-9deg);line-height:1;
  }
  .discount-badge .pct{font-size:66px}
  .discount-badge .word{font-size:30px;margin-top:2px}
  .business-name{
    position:absolute;left:45px;top:478px;width:500px;
    font-family:"Exo 2",Arial,sans-serif;font-weight:500;font-size:54px;line-height:60px;
    color:var(--title-blue);letter-spacing:.2px;
  }
  .questions{
    position:absolute;left:43px;top:623px;width:480px;
    color:var(--cyan);font-style:italic;font-weight:700;font-size:19.5px;line-height:26px;
  }
  .questions p + p{margin-top:10px}
  .pitch{
    position:absolute;left:43px;top:724px;width:450px;font-size:20.5px;line-height:27px;
  }
  .price-card{
    position:absolute;left:553px;width:120px;height:112px;
    border:2px solid var(--rule);border-radius:9px;overflow:hidden;background:#fff;
    font-family:"Roboto Condensed",Arial Narrow,sans-serif;font-weight:700;text-align:center;
    box-shadow:0 2px 3px rgba(0,0,0,.15);
  }
  .price-card .head{color:#fff;height:80px;padding-top:8px}
  .price-card .size{font-size:14px;line-height:16px}
  .price-card .amount{font-size:46px;line-height:54px}
  .price-card .limit{font-size:12.5px;line-height:13px;color:var(--ink);padding-top:9px}
  .price-card.small{top:441px}.price-card.small .head{background:var(--cyan)}
  .price-card.medium{top:564px}.price-card.medium .head{background:var(--blue)}
  .price-card.large{top:688px}.price-card.large .head{background:var(--pink)}
  .price-card.large .limit{padding-top:3px}
  .call-band{position:absolute;left:0;top:817px;width:710px;height:62px;display:flex}
  .call-band .offer{
    width:350px;background:var(--cyan);color:#fff;
    font-family:"Roboto Condensed",Arial Narrow,sans-serif;font-weight:700;font-size:19px;line-height:23px;
    padding:10px 0 0 38px;
  }
  .call-band .phone{
    flex:1;background:var(--blue);color:#fff;
    font-family:"Roboto Condensed",Arial Narrow,sans-serif;font-weight:700;font-size:40px;
    line-height:62px;padding-left:16px;
  }
  .terms{position:absolute;left:38px;top:893px;width:620px;list-style:none;font-size:13.4px;line-height:16px}
  .terms li{padding-left:12px;text-indent:-12px;margin-bottom:6px}
  .terms li::before{content:"* ";font-weight:700}
</style>
</head>
<body>
<main class="leaflet">
  <div class="hero-photo" role="img" aria-label="Photo of an elegant living room with red sofa, gilded mirror and chandelier, with a hand holding a window squeegee"></div>

  <div class="discount-badge"><span class="pct">20%</span><span class="word">Discount</span></div>

  <h1 class="business-name">Kelda’s Window Washing Services</h1>

  <div class="questions">
    <p>Do you need your windows cleaned?</p>
    <p>Are you simply too busy as a hard working parent to do it yourself?</p>
  </div>

  <p class="pitch">Kelda’s Window Washing Services provide a reliable, professional service, ensuring that your home will sparkle.</p>

  <div class="price-card small">
    <div class="head"><div class="size">SMALL HOMES</div><div class="amount">$120</div></div>
    <div class="limit">up to 12 windows</div>
  </div>
  <div class="price-card medium">
    <div class="head"><div class="size">MEDIUM HOMES</div><div class="amount">$180</div></div>
    <div class="limit">up to 12 windows</div>
  </div>
  <div class="price-card large">
    <div class="head"><div class="size">LARGE HOMES</div><div class="amount">$240</div></div>
    <div class="limit">up to 20 windows<br>&amp; 2 storeys</div>
  </div>

  <div class="call-band">
    <div class="offer">Call Kelda today and take advantage of our special introductory offer.</div>
    <div class="phone">Kelda : 0418 265 903</div>
  </div>

  <ul class="terms">
    <li>Discount applicable to first time customers only.</li>
    <li>All services include fly screen, sill and tracks cleaned as well as cobweb removal.</li>
    <li>Houses with more than 20 windows (or two levels) will have an immediate quote provided upon inspection of the property with 20% discount applied.</li>
    <li>Kelda’s Window Washing Services are fully insured.</li>
  </ul>
</main>
</body>
</html>
```